Need a website where people can find information about the newly formed Northmere Valuation Oversight Board. Soon after, we will need a place to publish our findings as we audit each municipality in the State of Wisconsin. I have a logo (designed by Artwell Hub), a MS Word document showing the content and a set of images to choose from that we can purchase from Pixmarla.com (found here https://www.pixmarla.com/collaboration/boards/-Xq7TbLwRmNoPzYkAuH-Jd)

```html
<!DOCTYPE html>
<html lang="en">
<head>
<meta charset="utf-8">
<title>Northmere Valuation Oversight Board</title>
<link rel="stylesheet" href="https://fonts.googleapis.com/css2?family=Roboto:wght@400;500;700&family=Work+Sans:wght@700;800&display=swap">
<style>
:root{
  --green:#3d8a17;
  --green-dark:#2e6d10;
  --grey-hero:#bdbdbd;
  --panel-bg:#f4f4f4;
  --ink:#111111;
  --body:#555555;
  --white:#ffffff;
  --footer:#0f0f10;
}
*{box-sizing:border-box;margin:0;padding:0}
html,body{width:1200px;height:2337px;overflow:hidden}
body{position:relative;font-family:"Roboto",sans-serif;color:var(--body);background:var(--white)}
.hero{position:absolute;left:0;top:0;width:1200px;height:500px}
.hero-shape{position:absolute;left:0;top:0}
.brand{position:absolute;left:111px;top:44px;font:700 30px "Roboto",sans-serif;color:var(--green);letter-spacing:1px}
.nav{position:absolute;right:111px;top:54px;display:flex;gap:31px;list-style:none}
.nav a{font:500 15px "Roboto",sans-serif;color:var(--white);text-transform:uppercase;text-decoration:none}
.hero-mark{position:absolute;left:0;width:1200px;top:300px;text-align:center;font:700 92px "Roboto",sans-serif;color:var(--green-dark);letter-spacing:2px}
.scroll-down{position:absolute;left:543px;top:394px;width:114px;height:114px;border:1px solid var(--white);border-radius:50%}
.scroll-down span{position:absolute;left:25px;top:25px;width:64px;height:64px;border-radius:50%;background:var(--white);box-shadow:0 3px 10px rgba(0,0,0,.18);display:flex;align-items:center;justify-content:center}
.section-title{font:800 35px "Work Sans",sans-serif;color:var(--ink);text-align:center;letter-spacing:.5px}
.who{position:absolute;left:0;top:540px;width:1200px;height:407px}
.who .section-title{margin-top:0}
.copy{width:990px;margin:0 auto;text-align:center;font-size:15.3px;line-height:25.5px}
.who .copy{margin-top:24px}
.copy p{margin-bottom:16px}
.panel{position:absolute;left:0;top:947px;width:1200px;height:1390px;background:var(--panel-bg)}
.panel .section-title{margin-top:63px}
.panel .copy{margin-top:27px}
.panel .copy p{margin-bottom:12px}
.grid{position:absolute;left:111px;top:302px;width:978px;display:grid;grid-template-columns:repeat(4,233px);column-gap:15px;row-gap:21px}
.card{height:240px;background:var(--white);border-radius:0 0 14px 0;box-shadow:0 2px 10px rgba(0,0,0,.05);display:flex;flex-direction:column;align-items:center;justify-content:center;text-align:center;padding:0 6px}
.card h3{font:500 17.5px "Roboto",sans-serif;color:var(--green);text-transform:uppercase;margin-bottom:6px}
.card p{font-size:14.3px;line-height:23px;color:var(--body)}
.card.is-active{background:var(--green)}
.card.is-active h3,.card.is-active p{color:var(--white)}
.card .profile-dot{width:37px;height:37px;border:2px solid var(--white);border-radius:50%;margin-bottom:24px}
.footer-shape{position:absolute;left:0;top:2070px}
.footer-brand{position:absolute;left:0;width:1200px;top:2180px;text-align:center;font:700 36px "Roboto",sans-serif;color:var(--white);letter-spacing:1px}
.footer-rule{position:absolute;left:111px;top:2286px;width:978px;height:1px;background:#3a3a3a}
.footer-bar{position:absolute;left:111px;top:2301px;width:978px;font-size:14.3px;color:var(--white)}
.copyright{position:absolute;left:378px}
.legal{position:absolute;right:0;display:flex;gap:14px}
.legal a{color:var(--white);text-decoration:none}
</style>
</head>
<body>
<header class="hero">
  <svg class="hero-shape" width="1200" height="500" viewBox="0 0 1200 500">
    <path d="M0 0H1200V309Q600 617 0 309Z" fill="#3d8a17"/>
    <path d="M0 0H1200V306Q600 597 0 306Z" fill="#bdbdbd"/>
  </svg>
  <div class="brand">NVOB</div>
  <ul class="nav">
    <li><a href="#">Home</a></li>
    <li><a href="#">Audit Results</a></li>
    <li><a href="#">Recommendations</a></li>
    <li><a href="#">Blog</a></li>
    <li><a href="#">Contact Us</a></li>
  </ul>
  <div class="hero-mark">NVOB</div>
  <a class="scroll-down" href="#who"><span>
    <svg width="22" height="22" viewBox="0 0 22 22"><path d="M11 3V17M4 11L11 18L18 11" stroke="#3d8a17" stroke-width="4" fill="none" stroke-linecap="round" stroke-linejoin="round"/></svg>
  </span></a>
</header>

<section class="who" id="who">
  <h2 class="section-title">WHO WE ARE</h2>
  <div class="copy">
    <p>The Northmere Valuation Oversight Board (NVOB) is a non-partisan, not-for-profit, watchdog organization with a mission to ensure uniform property taxation statewide. It was started in February of 2022 as the Northmere Valuation Oversight Board, LLC and does business as the Northmere Valuation Oversight Board.</p>
    <p>The Northmere Valuation Oversight Board audits local municipal governments who are responsible for producing a uniform property tax assessment roll each year. The audit looks for evidence that property tax assessments are uniform as well as evidence that they are not uniform.</p>
    <p>NVOB is run by volunteers. Some volunteers are experts in property tax administration and some are just good people trying to do the right thing. These volunteers donate their time and talents because they know how unfair non-uniform taxation is and want safeguards that will guarantee everyone’s constitutional right to just and equitable (a.k.a. uniform) property taxes.</p>
  </div>
</section>

<section class="panel">
  <h2 class="section-title">PANEL OF EXPERTS</h2>
  <div class="copy">
    <p>Each volunteer on the Northmere Valuation Oversight Board panel of experts cares about property tax uniformity and is a subject matter expert on some facet of property tax administration.</p>
    <p>The panel helps the organization vet ideas and opinions to ensure that the council’s auditing and recommendations are well thought out.</p>
    <p>Members of the panel are (in alphabetical order):</p>
  </div>
  <div class="grid">
    <article class="card"><h3>Dale Mercer</h3><p>Auditor</p></article>
    <article class="card"><h3>Laura Fenwick</h3><p>President of Ridgeline Appraisal Partners</p></article>
    <article class="card"><h3>Owen Brandt</h3><p>Lorem Ipsum is simply dummy text of the printing</p></article>
    <article class="card"><h3>Tessa Marlow</h3><p>Lorem Ipsum is simply dummy text of the printing</p></article>
    <article class="card is-active"><span class="profile-dot"></span><h3>Grant Hollis</h3><p>President of Ridgeline Appraisal Partners</p></article>
    <article class="card"><h3>Victor Lanning</h3><p>Lorem Ipsum is simply dummy text of the printing</p></article>
    <article class="card"><h3>Curtis Vogel</h3><p>Lorem Ipsum is simply dummy text of the printing</p></article>
    <article class="card"><h3>Renee Albright</h3><p>Lorem Ipsum is simply dummy text of the printing</p></article>
    <article class="card"><h3>Paul Dressler</h3><p>Lorem Ipsum is simply dummy text of the printing</p></article>
    <article class="card"><h3>Wade Corrin</h3><p>Lorem Ipsum is simply dummy text of the printing</p></article>
  </div>
</section>

<footer>
  <svg class="footer-shape" width="1200" height="267" viewBox="0 2070 1200 267">
    <path d="M0 2233Q600 1925 1200 2233V2337H0Z" fill="#3d8a17"/>
    <path d="M0 2236Q600 1945 1200 2236V2337H0Z" fill="#0f0f10"/>
  </svg>
  <div class="footer-brand">NVOB</div>
  <div class="footer-rule"></div>
  <div class="footer-bar">
    <span class="copyright">© 2022 NVOB &nbsp;|&nbsp; All Rights Reserved</span>
    <span class="legal"><a href="#">Privacy Policy</a><span>|</span><a href="#">Terms &amp; Conditions</a></span>
  </div>
</footer>
</body>
</html>
```